verdant terraces simple classy business card design

my name is colin barrow and I run a gardening business aimed at high class verdant terraces. the business name is verdant terraces and our logo was designed on pixel harbour .My clientel are anything from residential homes to businesses. I take pride in my work and know that I offer a service like no other in my area.
The business card will be used to represent my business and I want it to be not only rememberable, but simplistic and modern. Eye catching too. Of course I would like it relatable to gardening and appealing to the correct clientel - those being garden enthusiasts, prestigious homes and businesses that are after top of the line gardening services like no other on the market.
I am not a typical lawn mowing business so I don't want a typical card design that represents that. The gardens I work with are generally million dollar properties with owners who are very garden proud looking for upkeep and guidance from me along with sometimes whole new garden designs. I want the business cards to show to my clients that I take pride, as they do, in their garden. And I want them to know from my card that I am a professional, qualified horticulturist offering them a top of the line service for life. I want them to refer my business on. I want them to look at my business card and see class and professionalism in a modern unique bold way.
The card should be simple with the possibility of the logo on the front being embossed/debossed and my details on the back the card should have a organic garden feel it's very important to me that it is absolutely perfect
I am also very open to ideas and suggestions so look forward to seeing the designs. the business logo has been supplied with this project and I want the card to be double sided

Contact info is
Colin Barrow - Managing Director / Horticulturist
Phone : 0481 526 704
Email: colinbarrow@verdantterraces.example.au

Target Market(s)

high class gardens residential and commercial

Industry/Entity Type

Gardener

Contact Information for Business Card

Contact info is
Phone : 0481 526 704

PLEASE MAKE CARD DOUBLE SIDED

Requirements
Must have
• organic simple classy modern feel
• must flow with the current logo that has been supplied with this project
• Double sided
• Must explain in a simple way that I deal with high end gardens and I'm a qualified horticulturist
Nice to have
• embossed debossed logo
Should not have
• shouldn't be to busy or cheap looking

```html
<!DOCTYPE html>
<html lang="en">
<head>
<meta charset="utf-8">
<title>Verdant Terraces – Business Card</title>
<link href="https://fonts.googleapis.com/css2?family=Cinzel:wght@500&family=Open+Sans:wght@400;600&display=swap" rel="stylesheet">
<style>
  :root {
    --backdrop: #ebebe8;
    --card-light: #f0f0f0;
    --card-edge: #fafafa;
    --leaf-green: #5f9b50;
    --deep-green: #4f8a42;
    --emboss-green: #548f46;
    --pale-leaf: #dfe9da;
    --ink-grey: #3a3a3a;
    --white: #ffffff;
  }
  * { margin: 0; padding: 0; box-sizing: border-box; }
  html, body {
    width: 1200px; height: 900px; overflow: hidden;
    background: var(--backdrop);
  }
  .canvas { position: relative; width: 1200px; height: 900px; }

  .card {
    position: absolute;
    overflow: hidden;
    box-shadow: 0 2px 10px rgba(0,0,0,0.12);
  }

  /* Front side */
  .card-front {
    left: 237px; top: 62px; width: 556px; height: 342px;
    background: var(--card-edge);
  }
  .front-header {
    position: absolute; left: 0; top: 0; width: 100%; height: 163px;
    background: var(--card-light);
  }
  .wordmark {
    font-family: "Cinzel", "Times New Roman", serif;
    font-weight: 500;
    color: var(--deep-green);
    line-height: 1;
    white-space: nowrap;
  }
  .front-header .wordmark { position: absolute; left: 37px; top: 24px; }
  .wordmark-main { display: block; font-size: 36px; letter-spacing: 4.5px; }
  .wordmark-sub { display: block; font-size: 22px; letter-spacing: 23.5px; margin-top: 2px; }

  .holder-name {
    position: absolute; left: 37px; top: 108px;
    font-family: "Open Sans", Arial, sans-serif; font-weight: 600;
    font-size: 18px; color: var(--deep-green);
  }
  .holder-title {
    position: absolute; left: 37px; top: 131px;
    font-family: "Open Sans", Arial, sans-serif; font-weight: 400;
    font-size: 14px; color: var(--ink-grey);
  }

  .contact-band {
    position: absolute; left: 0; top: 163px; width: 100%; height: 165px;
    background: var(--leaf-green);
    color: var(--white);
    font-family: "Open Sans", Arial, sans-serif; font-size: 14px;
  }
  .address { position: absolute; left: 37px; top: 24px; line-height: 20px; }
  .contact-list { position: absolute; left: 37px; top: 86px; list-style: none; }
  .contact-list li { display: flex; align-items: center; height: 20px; }
  .contact-list svg { width: 10px; height: 10px; margin-right: 9px; fill: var(--white); }

  .tree-artwork {
    position: absolute; left: 425px; top: 160px; width: 131px; height: 168px;
    background: linear-gradient(180deg, var(--pale-leaf) 0%, var(--white) 55%, var(--pale-leaf) 100%);
  }

  /* Back side */
  .card-back {
    left: 459px; top: 518px; width: 560px; height: 342px;
    background: var(--leaf-green);
  }
  .back-mark {
    position: absolute; left: 230px; top: 84px; width: 100px; height: 100px;
    border-radius: 50%; background: var(--emboss-green);
  }
  .card-back .wordmark {
    position: absolute; left: 0; top: 188px; width: 100%; text-align: center;
    color: var(--emboss-green);
  }
  .card-back .wordmark-main { font-size: 42px; letter-spacing: 7px; }
  .card-back .wordmark-sub { font-size: 25px; letter-spacing: 30px; margin-top: 4px; padding-left: 30px; }
</style>
</head>
<body>
<main class="canvas">

  <section class="card card-front" aria-label="Business card front">
    <header class="front-header">
      <div class="wordmark">
        <span class="wordmark-main">VERDANT</span>
        <span class="wordmark-sub">TERRACES</span>
      </div>
      <p class="holder-name">Colin Barrow</p>
      <p class="holder-title">Managing Director / Horticulturist</p>
    </header>
    <div class="contact-band">
      <p class="address">12345, Address Goes Here<br>Country Name, 123456.</p>
      <ul class="contact-list">
        <li>
          <svg viewBox="0 0 10 10" aria-hidden="true"><path d="M2 0.5 L3.6 2.6 L2.8 3.6 C3.4 5 4.9 6.6 6.4 7.2 L7.4 6.4 L9.5 8 L8.4 9.5 C4.5 9.3 0.7 5.5 0.5 1.6 Z"/></svg>
          0481 526 704
        </li>
        <li>
          <svg viewBox="0 0 10 10" aria-hidden="true"><path d="M1 2.5 H9 V8 H1 Z" /><path d="M1 2.5 L5 5.6 L9 2.5" fill="none" stroke="#5f9b50" stroke-width="0.9"/></svg>
          colinbarrow@verdantterraces.example.au
        </li>
        <li>
          <svg viewBox="0 0 10 10" aria-hidden="true"><circle cx="5" cy="5" r="4.5"/><path d="M0.8 5 H9.2 M5 0.6 C3 3 3 7 5 9.4 M5 0.6 C7 3 7 7 5 9.4" fill="none" stroke="#5f9b50" stroke-width="0.7"/></svg>
          www.verdantterraces.example.au
        </li>
      </ul>
    </div>
    <div class="tree-artwork" role="img" aria-label="White tree illustration area"></div>
  </section>

  <section class="card card-back" aria-label="Business card back">
    <div class="back-mark"></div>
    <div class="wordmark">
      <span class="wordmark-main">VERDANT</span>
      <span class="wordmark-sub">TERRACES</span>
    </div>
  </section>

</main>
</body>
</html>
```